Kindle Your Clients Book Cover

A book main title will be, "Kindle Your Clients"
The subtext will be, "Go to market with a story that sizzles"
Would like it to blend with my web site brand. You can find it here: www.kindleyourclients.example

Audience is business and revenue leaders for small, medium and large businesses. They have a new solution, or want to enter a new market, and they need to "inspire their buyers" meaning getting the buyers to want to change enough to overcome their status quo bias. They need a story that sizzles to do this.

```html
<!DOCTYPE html>
<html lang="en">
<head>
<meta charset="utf-8">
<title>Kindle Your Clients – Book Cover Wrap</title>
<link rel="stylesheet" href="https://fonts.googleapis.com/css2?family=Outfit:wght@500;600;700&family=Questrial&display=swap">
<style>
  :root {
    --stage: #2b2b2b;
    --paper: #ffffff;
    --teal: #0fa89a;
    --ink: #333333;
    --body-ink: #3a3a3a;
    --photo-light: #efebe6;
    --photo-warm: #c9a98a;
    --photo-cool: #4f6470;
    --photo-deep: #2c3a44;
  }
  * { box-sizing: border-box; margin: 0; padding: 0; }
  html, body {
    width: 1200px; height: 1200px; overflow: hidden;
    background: var(--stage);
  }
  .cover-wrap {
    position: absolute; left: 30px; top: 200px;
    width: 1140px; height: 801px;
    background: var(--paper);
    font-family: "Outfit", sans-serif;
    color: var(--ink);
  }
  /* Back cover */
  .back-heading {
    position: absolute; left: 52px; width: 431px; top: 80px;
    text-align: center; font-weight: 600; font-size: 29px;
    letter-spacing: -0.8px; white-space: nowrap;
  }
  .accent { color: var(--teal); }
  .back-copy {
    position: absolute; left: 52px; top: 111px; width: 431px;
    font-family: "Questrial", sans-serif; font-size: 12.2px;
    line-height: 16.1px; color: var(--body-ink); text-align: justify;
  }
  .back-copy p + p { margin-top: 16px; }
  /* Spine */
  .spine-text {
    position: absolute; left: 569px; top: 59px;
    transform-origin: 0 0; transform: translate(17px, 0) rotate(90deg);
    white-space: nowrap; font-weight: 600; font-size: 34px;
    letter-spacing: -0.8px; line-height: 34px;
  }
  .spine-text .spine-author { margin-left: 42px; }
  /* Front cover */
  .front-title {
    position: absolute; left: 604px; width: 532px; top: 36px;
    text-align: center; font-weight: 600; font-size: 100px;
    line-height: 86px; letter-spacing: -3px;
  }
  .front-title .line { display: block; }
  .front-photo {
    position: absolute; left: 604px; top: 309px; width: 532px; height: 336px;
  }
  .front-subtitle {
    position: absolute; left: 604px; width: 532px; top: 660px;
    text-align: center; font-weight: 600; font-size: 24px;
    color: var(--teal); letter-spacing: -0.2px;
  }
  .front-author {
    position: absolute; left: 604px; width: 532px; top: 704px;
    text-align: center; font-weight: 600; font-size: 58px;
    letter-spacing: -0.5px; line-height: 66px;
  }
</style>
</head>
<body>
  <main class="cover-wrap">
    <section class="back-cover">
      <h2 class="back-heading"><span class="accent">KINDLE</span> YOUR CLIENTS</h2>
      <div class="back-copy">
        <p>Lorem ipsum dolor sit amet, consectetur adipiscing elit, sed do eiusmod tempor incididunt ut labore et dolore magna aliqua. Quis ipsum suspendisse ultrices gravida. Risus commodo viverra maecenas accumsan lacus vel facilisis. Lorem ipsum dolor sit amet, consectetur adipiscing elit, sed do eiusmod tempor incididunt ut labore et dolore magna aliqua. Quis ipsum suspendisse ultrices gravida. Risus commodo viverra maecenas accumsan lacus vel facilisis. Lorem ipsum dolor sit amet, consectetur adipiscing elit, sed do eiusmod tempor incididunt ut labore et dolore magna aliqua. Quis ipsum suspendisse ultrices gravida. Risus commodo viverra maecenas accumsan lacus vel facilisis.</p>
        <p>Lorem ipsum dolor sit amet, consectetur adipiscing elit, sed do eiusmod tempor incididunt ut labore et dolore magna aliqua. Quis ipsum suspendisse ultrices gravida. Risus commodo viverra maecenas accumsan lacus vel facilisis. Lorem ipsum dolor sit amet, consectetur adipiscing elit, sed do eiusmod tempor incididunt ut labore et dolore magna aliqua. Quis ipsum suspendisse ultrices gravida. Risus commodo viverra maecenas accumsan lacus vel facilisis. Lorem ipsum dolor sit amet, consectetur adipiscing elit, sed do eiusmod tempor incididunt ut labore et dolore magna aliqua. Quis ipsum suspendisse ultrices gravida. Risus commodo viverra maecenas accumsan lacus vel facilisis. Lorem ipsum dolor sit amet, consectetur adipiscing elit, sed do eiusmod tempor incididunt ut labore et dolore magna aliqua. Quis ipsum suspendisse ultrices gravida. Risus commodo viverra maecenas accumsan lacus vel facilisis.</p>
        <p>Lorem ipsum dolor sit amet, consectetur adipiscing elit, sed do eiusmod tempor incididunt ut labore et dolore magna aliqua. Quis ipsum suspendisse ultrices gravida. Risus commodo viverra maecenas accumsan lacus vel facilisis. Lorem ipsum dolor sit amet, consectetur adipiscing elit, sed do eiusmod tempor incididunt ut labore et dolore magna aliqua. Quis ipsum suspendisse ultrices gravida. Risus commodo viverra maecenas accumsan lacus vel facilisis. Lorem ipsum dolor sit amet, consectetur adipiscing elit, sed do eiusmod tempor incididunt ut labore et dolore magna aliqua. Quis ipsum suspendisse ultrices gravida. Risus commodo viverra maecenas accumsan lacus vel facilisis.</p>
      </div>
    </section>

    <section class="spine">
      <div class="spine-text"><span class="accent">KINDLE</span> YOUR CLIENTS<span class="spine-author">AUTHOR NAME</span></div>
    </section>

    <section class="front-cover">
      <h1 class="front-title">
        <span class="line accent">KINDLE</span>
        <span class="line">YOUR</span>
        <span class="line">CLIENTS</span>
      </h1>
      <svg class="front-photo" role="img" aria-label="Photo of a business handshake blended with a city skyline and rising candlestick chart bars" viewBox="0 0 532 336" preserveAspectRatio="none">
        <defs>
          <linearGradient id="photo-tone" x1="0" y1="0" x2="1" y2="0">
            <stop offset="0" stop-color="var(--photo-cool)"/>
            <stop offset="0.3" stop-color="var(--photo-light)"/>
            <stop offset="0.55" stop-color="var(--photo-warm)"/>
            <stop offset="0.8" stop-color="var(--photo-cool)"/>
            <stop offset="1" stop-color="var(--photo-deep)"/>
          </linearGradient>
          <linearGradient id="photo-fade" x1="0" y1="0" x2="0" y2="1">
            <stop offset="0" stop-color="#ffffff" stop-opacity="0.7"/>
            <stop offset="0.5" stop-color="#ffffff" stop-opacity="0.15"/>
            <stop offset="1" stop-color="#ffffff" stop-opacity="0"/>
          </linearGradient>
        </defs>
        <rect width="532" height="336" fill="url(#photo-tone)"/>
        <rect width="532" height="336" fill="url(#photo-fade)"/>
      </svg>
      <p class="front-subtitle">Go to market with a story that sizzles</p>
      <p class="front-author">AUTHOR NAME</p>
    </section>
  </main>
</body>
</html>
```